Landing Page and Logo for Auto-Blogging Platform

I created a platform that allows users to start a blog for their business, hobby, charity, etc. I need a landing page where users can learn about the platform, benefits of consistent blogging, SEO value, plans/pricing, etc. The landing page needs to have multiple call to action buttons encouraging the visitor to register/sign up for a free trial.

In addition to the landing page, I need a page for users to establish the settings for their blog. This page should be a fairly simple form, intended for the user to enter a few details to set up their blog:
1. Name of Blog
2. Up to 10 topics and/or keywords the blog should focus on
3. Theme: Color-scheme and logo upload for blog.

I have attached the specifications of the platform's functionality so you can better understand how it works, plans/pricing, etc.

I also need a logo for the business. The name of the platform is PostNook.

Target Market(s)

Website owners, bloggers, business owners

Industry/Entity Type

Technology, Internet, web design

Coding

Coded - Design and coding required

Number of Pages Required

2 page

Colors
0054AA
0677BA
7BADD7
CADEEF
E8F1F8
0094D4
00A9DD
6FCCEA
C7EBF8
E9F6FB

Requirements
Must have
• Eye-catching design but fairly light on content (keep it simple and brief.)
Nice to have
• Eye-catching yet simple design, clean and easy to understand what we are offering.
Should not have
• Too much “wordy” and confusing content.

```html
<!DOCTYPE html>
<html lang="en">
<head>
<meta charset="utf-8">
<title>PostNook — Start Your Blog</title>
<link rel="stylesheet" href="https://fonts.googleapis.com/css2?family=Outfit:wght@400;500;600;700&family=Poppins:wght@400;500;600;700&family=Inter:wght@400;500;600&display=swap">
<style>
:root{
  --navy:#0a1623;
  --navy-2:#0c1b2b;
  --primary:#0094D4;
  --sky:#00A9DD;
  --deep:#0054AA;
  --mid:#0677BA;
  --pale:#E8F1F8;
  --pill:#dde9f6;
  --pill-ink:#4f74a8;
  --ink:#161b24;
  --muted:#6b7280;
  --line:#e4e7ec;
  --grey-row:#e6e6e6;
  --peach:#fdf1ea;
  --star:#f5b50a;
  --head:'Outfit',sans-serif;
  --body:'Poppins',sans-serif;
  --text:'Inter',sans-serif;
}
*{box-sizing:border-box;margin:0;padding:0}
html,body{width:1200px;height:4098px;overflow:hidden}
body{position:relative;font-family:var(--body);color:var(--ink);background:#fff}
.abs{position:absolute}
.center{left:0;right:0;text-align:center}
.logo{font-family:var(--body);font-weight:500;color:#fff}

/* hero */
.hero{position:absolute;left:0;top:0;width:1200px;height:745px;
  background:
   radial-gradient(420px 260px at 90px 330px,rgba(0,148,212,.45),transparent 70%),
   radial-gradient(600px 260px at 620px 10px,rgba(0,120,180,.25),transparent 70%),
   radial-gradient(380px 300px at 1140px 420px,rgba(0,120,180,.18),transparent 70%),
   var(--navy);}
.nav-logo{left:145px;top:43px;font-size:20px}
.nav-links{left:404px;top:49px;display:flex;gap:27px;font-size:11px;color:#dfe6ee}
.nav-links .active{text-decoration:underline;text-underline-offset:4px}
.btn-signin{left:893px;top:37px;width:80px;height:38px;border:1px solid #5c6775;border-radius:5px;color:#fff;font-size:11px;display:flex;align-items:center;justify-content:center}
.btn-login{left:985px;top:37px;width:73px;height:36px;background:var(--primary);border-radius:5px;color:#fff;font-size:11px;display:flex;align-items:center;justify-content:center;font-weight:500}
.hero-badge{left:512px;top:145px;width:176px;height:26px;border-radius:13px;background:rgba(255,255,255,.08);display:flex;align-items:center;justify-content:center;gap:8px;color:#dfe6ee;font-size:9.5px;letter-spacing:1.4px;font-weight:500}
.hero-title{top:182px;font-family:var(--head);font-weight:600;font-size:46px;line-height:52px;color:#fff}
.hero-title .accent{color:#1ea4ea}
.hero-sub{top:303px;font-size:13px;color:#e3e8ee}
.btn-trial{left:433px;top:349px;width:213px;height:46px;background:var(--primary);border-radius:4px;color:#fff;font-size:12.5px;font-weight:500;display:flex;align-items:center;justify-content:center}
.btn-more{left:659px;top:349px;width:110px;height:46px;border:1px solid #cfd6de;border-radius:4px;color:#fff;font-size:12.5px;display:flex;align-items:center;justify-content:center}
.hero-arrow{top:610px;color:#8fa0b3;font-size:18px}
.devices{left:226px;top:440px;width:750px;height:470px}

/* trusted */
.trusted{left:185px;top:918px;width:761px;height:149px;background:var(--peach)}
.trusted h3{position:absolute;left:0;right:0;top:14px;text-align:center;font-family:var(--text);font-weight:400;font-size:20px;color:#2a2f38}
.brand{position:absolute;top:91px;transform:translateX(-50%);font-family:var(--body);font-weight:600;font-size:15px;color:#8792a3;white-space:nowrap}

/* section heads */
.pill{position:absolute;transform:translateX(-50%);height:24px;padding:0 16px;border-radius:12px;background:var(--pill);color:var(--pill-ink);font-size:9px;letter-spacing:1.6px;font-weight:500;display:flex;align-items:center;white-space:nowrap}
.sec-title{position:absolute;left:0;right:0;text-align:center;font-family:var(--head);font-weight:600;font-size:32px;color:var(--ink)}

/* why us */
.why{position:absolute;top:1202px;width:300px;transform:translateX(-50%);text-align:center}
.why .ring{width:78px;height:78px;margin:0 auto;border-radius:50%;border:5px solid var(--deep);border-left-color:#cde0f3;display:flex;align-items:center;justify-content:center}
.why h4{margin-top:22px;font-size:17px;font-weight:600}
.why p{margin-top:8px;font-size:11.5px;line-height:17px;color:var(--muted)}

/* benefits */
.benefits{position:absolute;left:0;top:1476px;width:1200px;height:700px;overflow:hidden;
  background:
   radial-gradient(360px 300px at 60px 300px,rgba(0,148,212,.4),transparent 70%),
   radial-gradient(360px 300px at 1150px 260px,rgba(0,120,190,.3),transparent 70%),
   var(--navy-2);}
.benefits .pill{background:#0f3852;color:#2aa6dd}
.benefits .sec-title{color:#fff}
.benefit{position:absolute;top:228px;display:flex;gap:14px}
.benefit h4{color:#fff;font-size:14.5px;font-weight:600}
.benefit p{margin-top:4px;color:#c7cfd9;font-size:11.5px;line-height:17px;width:235px}

/* dashboard */
.dash{position:absolute;left:167px;top:358px;width:866px;height:400px;border-radius:18px;background:#3a4550;padding:9px}
.dash-in{position:relative;width:100%;height:100%;background:#fff;border-radius:12px;overflow:hidden;font-size:11px;color:#333}
.d-logo{left:12px;top:20px;font-size:14px;color:#222;font-weight:500}
.d-search{left:165px;top:11px;width:197px;height:27px;border-radius:14px;background:#eef1f6;color:#6a7ec8;font-size:11px;padding:6px 12px}
.d-welcome{left:526px;top:19px;font-size:11.5px}
.d-welcome b{color:#5b4bd6}
.d-toggle{left:778px;top:12px;width:63px;height:26px;border-radius:13px;background:#f0f2f5}
.d-side{left:0;top:52px;width:145px;height:400px;border-right:1px solid #eef0f3}
.d-menu{position:absolute;left:12px;font-size:11px;color:#333;display:flex;align-items:center;gap:10px;white-space:nowrap}
.d-menu i{display:inline-block;width:12px;height:12px;border:1.5px solid #555;border-radius:3px}
.d-label{position:absolute;left:12px;color:#777;font-size:11px}
.thumb{background:linear-gradient(135deg,#5a6f88,#b89078)}
.d-h{position:absolute;font-weight:600;font-size:12px;line-height:15px;color:#111}
.d-small{position:absolute;font-size:7px;line-height:10px;color:#9aa}
.fav{position:absolute;left:685px;display:flex;gap:10px;align-items:center}
.fav .thumb{width:24px;height:24px;border-radius:3px}
.fav b{display:block;color:#5b4bd6;font-weight:600;font-size:9.5px}
.fav span{font-size:9.5px;color:#333}

/* pricing */
.base-card{left:185px;top:2364px;width:250px;height:393px;border-radius:12px;background:linear-gradient(180deg,#0a8fd6,#0057ab);color:#fff;text-align:center}
.plan-col{position:absolute;top:2364px;text-align:center}
.plan-name{position:absolute;left:0;right:0;top:100px;font-size:15px;font-weight:600;text-align:center}
.plan-price{position:absolute;left:0;right:0;top:124px;font-size:27px;font-weight:700;text-align:center}
.plan-price small{font-size:11px;font-weight:600}
.plan-icon{position:absolute;left:50%;top:28px;transform:translateX(-50%)}
.row{position:absolute;left:435px;width:579px;height:42px}
.row.grey{background:var(--grey-row)}
.cell{position:absolute;height:42px;display:flex;align-items:center;justify-content:center;font-size:11px;color:#555}
.base-row{position:absolute;left:185px;width:250px;height:42px;display:flex;align-items:center;justify-content:center;font-size:11px;color:#fff}
.plan-btn{position:absolute;top:2684px;width:150px;height:48px;border-radius:4px;background:linear-gradient(180deg,#0a8fd6,#0068b8);color:#fff;font-size:13px;display:flex;align-items:center;justify-content:center}
.plan-btn.white{background:#fff;color:var(--primary)}
.col-divider{position:absolute;left:724px;top:2539px;width:1px;height:123px;background:#d2d2d2}

/* testimonials */
.tcard{position:absolute;top:2994px;width:300px}
.avatar{position:absolute;left:0;top:0;width:46px;height:46px;border-radius:50%;background:linear-gradient(135deg,#b9c2cc,#7b8793)}
.tname{position:absolute;left:55px;top:8px;font-family:var(--text);font-weight:500;font-size:13px}
.tmeta{position:absolute;left:55px;top:28px;font-size:9px;color:#333;white-space:nowrap}
.tmeta .stars{color:var(--star);letter-spacing:1px;font-size:10px;margin-right:4px}
.tbody{position:absolute;left:0;top:68px;width:300px;font-family:var(--text);font-size:12.5px;line-height:21.2px;color:#333}
.fade-l{left:0;top:2960px;width:200px;height:340px;background:linear-gradient(90deg,rgba(255,255,255,.95),rgba(255,255,255,.55))}
.fade-r{left:1080px;top:2960px;width:120px;height:340px;background:linear-gradient(270deg,rgba(255,255,255,.95),rgba(255,255,255,.55))}
.t-arrow{position:absolute;top:3107px;width:36px;height:36px;border-radius:50%;background:var(--deep);display:flex;align-items:center;justify-content:center}
.dots{left:572px;top:3299px;display:flex;gap:6px}
.dots i{width:7px;height:7px;border-radius:50%;background:#cdd9e8}
.dots i.on{background:var(--deep)}

/* cta */
.cta-bg{left:0;top:3343px;width:1200px;height:510px}
.cta-photo{left:150px;top:3372px;width:300px;height:470px;border-radius:150px 150px 40px 40px;background:linear-gradient(180deg,#e7b48c,#e86b7a 55%,#c9c9c9)}
.cta-pill{left:562px;top:3515px;height:24px;padding:0 22px;border-radius:12px;background:#2f7fd0;color:#e6f1fb;font-size:9px;letter-spacing:1.6px;display:flex;align-items:center}
.cta-title{left:562px;top:3550px;font-family:var(--head);font-weight:600;font-size:31px;line-height:38px;color:#fff}
.cta-text{left:562px;top:3670px;width:420px;font-size:12.5px;line-height:17px;color:#e8f0fa}
.cta-btn{left:562px;top:3727px;width:215px;height:46px;background:#fff;border-radius:4px;color:var(--deep);font-size:12.5px;font-weight:500;display:flex;align-items:center;justify-content:center}

/* footer */
.footer{left:0;top:3853px;width:1200px;height:245px;background:var(--navy-2)}
.f-logo{left:145px;top:64px;font-size:29px}
.f-links{right:142px;top:76px;display:flex;gap:30px;font-size:11px;color:#e0e6ec}
.f-line{left:145px;top:133px;width:913px;height:1px;background:#26323f}
.f-copy{top:179px;font-size:10.5px;color:#b7c0cb}
</style>
</head>
<body>

<!-- HERO -->
<header class="hero">
  <div class="abs logo nav-logo">PostNook</div>
  <nav class="abs nav-links">
    <span class="active">Home</span><span>Features</span><span>Pricing</span><span>How It Works</span><span>Blog</span><span>Resources</span>
  </nav>
  <div class="abs btn-signin">Sign in</div>
  <div class="abs btn-login">Login</div>

  <div class="abs hero-badge">
    <svg width="16" height="16" viewBox="0 0 16 16"><circle cx="8" cy="8" r="7" fill="none" stroke="#1ea4ea" stroke-width="1.4"/><path d="M4.8 8.2l2.1 2.1 4.2-4.4" fill="none" stroke="#1ea4ea" stroke-width="1.4"/></svg>
    WELCOME TO POSTNOOK
  </div>
  <h1 class="abs center hero-title">Transform Your Passion<br>into a Powerful <span class="accent">Blog with PostNook</span></h1>
  <p class="abs center hero-sub">Create, manage, and grow your blog effortlessly. Perfect for businesses, hobbies, and more.</p>
  <div class="abs btn-trial">Start Your 15 days Free Trial</div>
  <div class="abs btn-more">Learn More</div>
  <div class="abs hero-arrow" style="left:145px">&#8249;</div>
  <div class="abs hero-arrow" style="left:1048px">&#8250;</div>
</header>

<svg class="abs devices" viewBox="0 0 750 470" role="img" aria-label="Two tablets showing the PostNook blog dashboard with article cards and playlists">
  <defs>
    <linearGradient id="scr" x1="0" y1="0" x2="1" y2="1">
      <stop offset="0" stop-color="#f4f6f9"/><stop offset=".6" stop-color="#e3e8ee"/><stop offset="1" stop-color="#c9a79a"/>
    </linearGradient>
  </defs>
  <g transform="rotate(-12 260 300)">
    <rect x="20" y="150" width="440" height="290" rx="22" fill="#dfe3e8" stroke="#8f98a3" stroke-width="3"/>
    <rect x="36" y="164" width="408" height="262" rx="10" fill="url(#scr)"/>
  </g>
  <g transform="rotate(12 500 180)">
    <rect x="290" y="30" width="440" height="290" rx="22" fill="#dfe3e8" stroke="#8f98a3" stroke-width="3"/>
    <rect x="306" y="44" width="408" height="262" rx="10" fill="url(#scr)"/>
  </g>
</svg>

<!-- TRUSTED -->
<section class="abs trusted">
  <h3>Trusted by More Than 100 Brands</h3>
  <span class="brand" style="left:116px">Brightmind</span>
  <span class="brand" style="left:240px">Groupline</span>
  <span class="brand" style="left:351px">Ipora</span>
  <span class="brand" style="left:476px">Norvan</span>
  <span class="brand" style="left:603px">Ostrova</span>
  <span class="brand" style="left:703px">Univera</span>
</section>

<!-- WHY US -->
<span class="pill" style="left:600px;top:1101px">WHY US?</span>
<h2 class="sec-title" style="top:1130px">Why Choose PostNook?</h2>

<div class="why" style="left:298px">
  <div class="ring"><svg width="32" height="32" viewBox="0 0 32 32" fill="none" stroke="#0054AA" stroke-width="1.6"><path d="M11 16a5 5 0 1110 0c0 2-1.5 3-2 5h-6c-.5-2-2-3-2-5z"/><path d="M13 24h6M14 27h4M16 4v3M6 8l2 2M26 8l-2 2M3 16h3M26 16h3"/></svg></div>
  <h4>Simplicity</h4>
  <p>No coding required. Our platform makes it easy<br>for anyone to start and manage a blog.</p>
</div>
<div class="why" style="left:600px">
  <div class="ring"><svg width="32" height="32" viewBox="0 0 32 32" fill="none" stroke="#0054AA" stroke-width="1.6"><rect x="8" y="5" width="16" height="22" rx="2"/><path d="M12 11h8M12 15h8M12 19h5"/><circle cx="22" cy="22" r="4"/></svg></div>
  <h4>Customization</h4>
  <p>Personalize your blog with your brand's colors,<br>logo, and style.</p>
</div>
<div class="why" style="left:904px">
  <div class="ring"><svg width="32" height="32" viewBox="0 0 32 32" fill="none" stroke="#0054AA" stroke-width="1.6"><path d="M12 20c2-9 8-14 14-15-1 6-6 12-15 14z"/><circle cx="20" cy="12" r="2"/><path d="M12 20l-4 4M9 16l-4 1M16 23l-1 4"/></svg></div>
  <h4>SEO Optimized</h4>
  <p>Improve your online visibility with our built-in<br>SEO tools.</p>
</div>

<!-- BENEFITS -->
<section class="benefits">
  <span class="pill" style="left:600px;top:82px">BENEFITS OF BLOGGING</span>
  <h2 class="sec-title" style="top:113px">Why Consistent Blogging Matters</h2>

  <div class="benefit" style="left:153px">
    <svg width="46" height="46" viewBox="0 0 46 46" fill="none" stroke="#2aa6dd" stroke-width="1.6"><rect x="4" y="10" width="30" height="24" rx="2"/><path d="M10 28v-6M16 28v-10M22 28v-8M28 28v-12"/><circle cx="34" cy="30" r="7"/><path d="M39 35l5 5"/></svg>
    <div><h4>Boost Your SEO</h4><p>Increase your search engine rankings<br>with regular, keyword-rich content.</p></div>
  </div>
  <div class="benefit" style="left:482px">
    <svg width="46" height="46" viewBox="0 0 46 46" fill="none" stroke="#2aa6dd" stroke-width="1.6"><rect x="8" y="4" width="26" height="38" rx="2"/><circle cx="21" cy="15" r="5"/><path d="M14 26h14M14 31h14M14 36h9"/></svg>
    <div><h4>Build Authority</h4><p>Establish your brand as a leader in<br>your industry.</p></div>
  </div>
  <div class="benefit" style="left:780px">
    <svg width="46" height="46" viewBox="0 0 46 46" fill="none" stroke="#2aa6dd" stroke-width="1.6"><circle cx="23" cy="16" r="5"/><circle cx="11" cy="22" r="4"/><circle cx="35" cy="22" r="4"/><path d="M14 38c0-6 4-10 9-10s9 4 9 10M3 38c0-5 3-8 8-8M43 38c0-5-3-8-8-8"/></svg>
    <div><h4>Engage Your Audience</h4><p>Connect with your audience through<br>valuable and relevant content.</p></div>
  </div>

  <div class="dash">
    <div class="dash-in">
      <div class="abs d-logo">PostNook</div>
      <div class="abs d-search">Search</div>
      <div class="abs d-welcome">Welcome <b>Priya</b></div>
      <div class="abs d-toggle"></div>

      <div class="abs d-side">
        <span class="d-label" style="top:12px">Menu</span>
        <span class="d-menu" style="top:40px;color:#5b4bd6;font-weight:600"><i style="border-color:#5b4bd6"></i>Home</span>
        <span class="d-menu" style="top:70px"><i></i>Library</span>
        <span class="d-menu" style="top:100px"><i style="border-radius:50%"></i>Discover</span>
        <span class="d-label" style="top:144px">Playlist</span>
        <span class="d-menu" style="top:174px"><i class="thumb" style="border:0"></i>Chill Pill</span>
        <span class="d-menu" style="top:204px"><i class="thumb" style="border:0"></i>Best of Kiran</span>
        <span class="d-menu" style="top:234px"><i class="thumb" style="border:0"></i>Global Hits</span>
        <span class="d-menu" style="top:264px"><i class="thumb" style="border:0"></i>Ravi Sen Vibes</span>
      </div>

      <div class="d-h" style="left:162px;top:92px;width:120px">Short Sentences Gives You the Liberty</div>
      <div class="d-small" style="left:162px;top:148px;width:120px">Paradoxically, using more short sentences gives you the liberty to write beautiful long sentences.<br><br>But in a way that's never been done before.</div>
      <div class="d-small" style="left:162px;top:222px;color:#777">Mark Dale</div>
      <div class="d-h" style="left:162px;top:272px;width:110px">5 Ways to Improve your Life.</div>

      <div class="abs thumb" role="img" aria-label="Photo of a person on a mountain ridge" style="left:297px;top:89px;width:146px;height:98px;border-radius:4px;background:linear-gradient(180deg,#aab6c2,#5d6a76)"></div>
      <div class="d-h" style="left:299px;top:203px;width:145px;font-size:10.5px;line-height:13px">How to Build a $24 Billion Dollar Company in Just 2 Years.</div>
      <div class="d-small" style="left:299px;top:250px;width:145px">I've come to the conclusion that 50% of folks in this world don't ever spend enough time alone with their thoughts to have their own opinions.</div>

      <div class="abs thumb" role="img" aria-label="Photo of a person at a window" style="left:468px;top:89px;width:103px;height:69px;border-radius:4px;background:linear-gradient(180deg,#2e3a48,#8a6d58)"></div>
      <div class="d-h" style="left:470px;top:172px;width:100px;font-size:10.5px;line-height:13px">8 Powerful Mental Models to Help You Win.</div>
      <div class="d-small" style="left:470px;top:216px">By Andrew Peterson</div>
      <div class="abs thumb" role="img" aria-label="Photo of a rocky coastline" style="left:468px;top:238px;width:103px;height:60px;border-radius:4px;background:linear-gradient(180deg,#4b8fb8,#2f5b44)"></div>
      <div class="d-h" style="left:470px;top:306px;font-size:10.5px">High performers</div>

      <div class="d-small" style="left:600px;top:92px;width:52px;color:#555"><b>Podcasts</b><br>An interview with a tech founder.</div>
      <div class="d-small" style="left:600px;top:162px;width:52px;color:#555"><b>Interviews</b><br>Make $500k through small biz or raise it from family.</div>
      <div class="d-small" style="left:600px;top:248px;width:52px;color:#555"><b>Podcasts</b><br>Lengthen your time horizon.</div>

      <div class="abs" style="left:676px;top:52px;width:1px;height:340px;background:#eef0f3"></div>
      <div class="abs" style="left:685px;top:62px;font-weight:600;font-size:11.5px">Favorite</div>
      <div class="fav" style="top:90px"><i class="thumb"></i><div><b>Silver Lanes</b><span>Aman Verghese</span></div></div>
      <div class="fav" style="top:125px"><i class="thumb"></i><div><b>Golden Hour</b><span>Dev Kumar, R. Anand</span></div></div>
      <div class="fav" style="top:160px"><i class="thumb"></i><div><b>Blue Monsoon</b><span>Kabir Aulakh</span></div></div>
      <div class="fav" style="top:195px"><i class="thumb"></i><div><b>Night Train</b><span>Mohan Chand, Jai Alvi</span></div></div>
      <div class="fav" style="top:230px"><i class="thumb"></i><div><b>One Morning</b><span>Yash Shankar</span></div></div>
      <div class="abs" style="left:685px;top:276px;font-weight:600;font-size:11.5px">Top Artists</div>
      <div class="abs thumb" style="left:685px;top:298px;width:150px;height:40px;border-radius:4px"></div>
    </div>
  </div>
</section>

<!-- PRICING -->
<span class="pill" style="left:600px;top:2260px">PLANS &amp; PRICING</span>
<h2 class="sec-title" style="top:2289px">Flexible Plans for Every Need</h2>

<div class="row grey" style="top:2539px"></div>
<div class="row" style="top:2581px"></div>
<div class="row grey" style="top:2620px"></div>
<div class="col-divider"></div>

<div class="abs base-card">
  <svg class="plan-icon" width="56" height="56" viewBox="0 0 56 56" fill="none" stroke="#fff" stroke-width="1.8"><circle cx="36" cy="16" r="10"/><path d="M36 11v10M33 13h5a2 2 0 010 4h-4a2 2 0 000 4h5"/><rect x="6" y="30" width="8" height="18" rx="1"/><path d="M14 33h8l10-4a3 3 0 012 5l-10 5h-10M14 45h12l16-9"/></svg>
  <div class="plan-name">Base Plan</div>
  <div class="plan-price">$9.99<small>/mo</small></div>
</div>
<div class="base-row" style="top:2539px;background:rgba(255,255,255,.14)">1 blog post</div>
<div class="base-row" style="top:2581px">up to 2,000 words</div>
<div class="base-row" style="top:2620px;background:rgba(255,255,255,.1)">Every Month</div>

<div class="plan-col" style="left:435px;width:289px;height:170px">
  <svg class="plan-icon" width="56" height="56" viewBox="0 0 56 56" fill="none" stroke="#8a8a8a" stroke-width="1.4"><path d="M14 16h28l8 10-22 24L6 26z"/><path d="M6 26h44M22 16l-4 10 10 24 10-24-4-10"/><path d="M28 4v6M16 7l3 4M40 7l-3 4"/></svg>
  <div class="plan-name">Premium Plan</div>
  <div class="plan-price">$14.99<small>/mo</small></div>
</div>
<div class="plan-col" style="left:724px;width:290px;height:170px">
  <svg class="plan-icon" width="56" height="56" viewBox="0 0 56 56" fill="none" stroke="#8a8a8a" stroke-width="1.4"><path d="M28 6l5 4 6-1 2 6 5 4-2 6 2 6-5 4-2 6-6-1-5 4-5-4-6 1-2-6-5-4 2-6-2-6 5-4 2-6 6 1z"/><path d="M28 18l3 6 6 1-4 4 1 6-6-3-6 3 1-6-4-4 6-1z"/></svg>
  <div class="plan-name">Ultimate Plan</div>
  <div class="plan-price">$24.99<small>/mo</small></div>
</div>

<div class="cell" style="left:435px;width:289px;top:2539px">1 blog post</div>
<div class="cell" style="left:435px;width:289px;top:2581px">up to 2,000 words</div>
<div class="cell" style="left:435px;width:289px;top:2620px">Every Week</div>
<div class="cell" style="left:724px;width:290px;top:2539px">1 blog post</div>
<div class="cell" style="left:724px;width:290px;top:2581px">(up to 3,000 words) per day</div>
<div class="cell" style="left:724px;width:290px;top:2620px">Unlimited Manual Posting</div>

<div class="plan-btn white" style="left:235px">Choose Plan</div>
<div class="plan-btn" style="left:505px">Choose Plan</div>
<div class="plan-btn" style="left:795px">Choose Plan</div>

<!-- TESTIMONIALS -->
<span class="pill" style="left:600px;top:2858px">TESTIMONIALS</span>
<h2 class="sec-title" style="top:2889px">Hear from Our Happy Users</h2>

<div class="tcard" style="left:-190px">
  <div class="avatar" role="img" aria-label="User portrait"></div>
  <div class="tname">Daniel D.</div>
  <div class="tmeta"><span class="stars">★★★★★</span>1 month ago</div>
  <div class="tbody" style="text-align:right;width:298px">They were a great guide finding the<br>right home for you. We sold our<br>old place at a great price!<br>Thanks to our Realtor, we<br>found a team who helped us<br>move fast. The process was</div>
</div>

<div class="tcard" style="left:172px">
  <div class="avatar" role="img" aria-label="Portrait of Emily R."></div>
  <div class="tname">Emily R.</div>
  <div class="tmeta"><span class="stars">★★★★★</span>1 month ago</div>
  <div class="tbody">It is a long established fact that a reader will be distracted by the read able content of a page when looking at its layout. The point of using Lorem Ipsum is that it has a more-or-less normal distribution of letters, as op posed to using 'Content here, content here', making it look...</div>
</div>
<div class="tcard" style="left:480px">
  <div class="avatar" role="img" aria-label="Portrait of Sarah and John D."></div>
  <div class="tname">Sarah &amp; John D.</div>
  <div class="tmeta"><span class="stars">★★★★★</span>1 month ago</div>
  <div class="tbody">It is a long established fact that a reader will be distracted by the read able content of a page when looking at its layout. The point of using Lorem Ipsum is that it has a more-or-less normal distribution of letters, as op posed to using 'Content here,...</div>
</div>
<div class="tcard" style="left:788px">
  <div class="avatar" role="img" aria-label="Portrait of Jessica T."></div>
  <div class="tname">Jessica T.</div>
  <div class="tmeta"><span class="stars">★★★★★</span>1 month ago</div>
  <div class="tbody">It is a long established fact that a reader will be distracted by the read able content of a page when looking at its layout. The point of using Lorem Ipsum is that it has a more-or-less normal distribution of letters, as op posed to using 'Content here, content here', making it look...</div>
</div>
<div class="tcard" style="left:1096px">
  <div class="avatar" role="img" aria-label="User portrait"></div>
  <div class="tname">Sarah L.</div>
  <div class="tmeta"><span class="stars">★★★★★</span>1 month ago</div>
  <div class="tbody">Our Denver Realtor was the perfect realtor to sell our home quickly. Thanks to Our team we found a fantastic place to buy our dream home. It was smooth and simple.</div>
</div>

<div class="abs fade-l"></div>
<div class="abs fade-r"></div>
<div class="t-arrow" style="left:132px"><svg width="16" height="16" viewBox="0 0 16 16" fill="none" stroke="#fff" stroke-width="1.8"><path d="M13 8H3M7 4L3 8l4 4"/></svg></div>
<div class="t-arrow" style="left:1033px"><svg width="16" height="16" viewBox="0 0 16 16" fill="none" stroke="#fff" stroke-width="1.8"><path d="M3 8h10M9 4l4 4-4 4"/></svg></div>
<div class="abs dots"><i></i><i class="on"></i><i></i><i></i></div>

<!-- CTA -->
<svg class="abs cta-bg" viewBox="0 0 1200 510" preserveAspectRatio="none">
  <path d="M0 420 C120 330 260 300 380 250 C470 210 520 140 600 120 L600 510 L0 510Z" fill="#1a8fe4"/>
  <path d="M560 200 C560 110 640 60 760 70 C880 80 980 30 1090 40 C1190 50 1210 160 1170 250 C1140 320 1160 390 1180 450 L1180 470 L620 470 C560 470 540 420 560 380 C580 330 560 270 560 200Z" fill="#0a5bb5"/>
  <path d="M0 470 L1200 470 L1200 510 L0 510Z" fill="#1a8fe4"/>
  <circle cx="957" cy="100" r="17" fill="#fff" stroke="#0094D4" stroke-width="5"/>
</svg>
<div class="abs cta-photo" role="img" aria-label="Smiling woman sitting cross-legged with a laptop"></div>
<div class="abs cta-pill">CONTACT US</div>
<h2 class="abs cta-title">Transform Your Ideas<br>into Reality – Sign Up for<br>a Free Trial!</h2>
<p class="abs cta-text">Everything you need to create and grow your blog. SEO tools, analytics, and more at your fingertips.</p>
<div class="abs cta-btn">Start Your 15 days Free Trial</div>

<!-- FOOTER -->
<footer class="abs footer">
  <div class="abs logo f-logo">PostNook</div>
  <nav class="abs f-links"><span>Home</span><span>Features</span><span>Pricing</span><span>How It Works</span><span>Blog</span><span>Resources</span><span>Contact Us</span></nav>
  <div class="abs f-line"></div>
  <p class="abs center f-copy">© 2024 PostNook. All rights reserved.</p>
</footer>

</body>
</html>
```